Business Cards

Need business card design that I can update for new employees and details. Needs to incorporate our logo, be bright and fun (in line with tourism and holidays)
Would like a Map of Western Australia on the front with locations all the caravan parks we own (just purchased Tom Price so please include that as well as others listed on our website).
Target Market(s)
Famillies
Contact Information for Business Card
5 Cards -
Neil Perrow (Director) e: perrow@wattlebay.com.au p: 0491 570 156
Mira Perrow (Director) e: perrow@wattlebay.com.au p: 0491 570 157
Owen Halvey (General Manager) e: halvey@wattlebay.com.au p: 0491 570 158
Helen Halvey (General Manager) e: halvey@wattlebay.com.au p: 0491 570 159
Colin Danby (Training and Operations Manager) - e: danby@wattlebay.com.au p:0491 570 110
Colors
Look and feel

```html
<!DOCTYPE html>
<html lang="en">
<head>
<meta charset="utf-8">
<title>Wattle Bay Tourist Parks – Business Card</title>
<link rel="stylesheet" href="https://fonts.googleapis.com/css2?family=Roboto:wght@400;500&display=swap">
<style>
  :root {
    --backdrop: #b4b4b4;
    --card-dark: #1b1c1e;
    --card-light: #f1f1f1;
    --teal: #40bfcd;
    --sea-green: #6bbdae;
    --ink: #454545;
    --rule: #4a4a4a;
    --white: #ffffff;
  }
  * { margin: 0; padding: 0; box-sizing: border-box; }
  html, body { width: 1200px; height: 960px; overflow: hidden; }
  body {
    position: relative;
    background: var(--backdrop);
    font-family: "Roboto", Arial, sans-serif;
  }
  .card { position: absolute; left: 320px; width: 600px; }

  /* Back of card */
  .card-back { top: 102px; height: 348px; background: var(--card-dark); }
  .card-back .brand-mark {
    position: absolute; left: 228px; top: 104px;
    width: 148px; height: 148px;
    background: var(--teal);
    border: 4px solid var(--white);
  }
  .card-back .brand-name {
    position: absolute; left: 0; right: 0; top: 262px;
    text-align: center; color: var(--white);
    font-size: 20px; font-weight: 400; letter-spacing: 5px;
  }
  .card-back .web {
    position: absolute; left: 0; right: 0; top: 300px;
    text-align: center; color: var(--white);
    font-size: 14px; letter-spacing: 3.2px;
  }

  /* Front of card */
  .card-front { top: 493px; height: 343px; background: var(--card-light); overflow: hidden; }
  .brand-lockup { position: absolute; right: 36px; top: 37px; width: 222px; text-align: center; }
  .brand-lockup .brand-mark {
    display: block; margin: 0 auto 8px;
    width: 70px; height: 70px;
    background: var(--teal); border: 2px solid var(--white);
    outline: 1px solid var(--teal);
  }
  .brand-lockup .brand-name {
    color: var(--ink); font-size: 26px; font-weight: 400;
    letter-spacing: 3px; line-height: 30px; text-transform: uppercase;
  }
  .brand-lockup .brand-name small {
    display: block; font-size: 12px; letter-spacing: 2.6px; line-height: 14px;
  }
  .person { position: absolute; left: 37px; top: 190px; }
  .person .name { color: var(--teal); font-size: 20px; font-weight: 500; line-height: 22px; }
  .person .role { color: var(--sea-green); font-size: 15px; font-weight: 400; margin-top: 3px; }
  .divider { position: absolute; left: 37px; right: 37px; top: 240px; height: 1px; background: var(--rule); }
  .contact { position: absolute; left: 37px; top: 252px; list-style: none; }
  .contact li {
    display: flex; align-items: center; gap: 9px;
    height: 19.5px; color: var(--ink); font-size: 14.5px;
  }
  .contact svg { width: 13px; height: 13px; fill: var(--teal); flex: none; }
  .footer-band { position: absolute; left: 0; right: 0; bottom: 0; height: 13px; }
</style>
</head>
<body>

<section class="card card-back" aria-label="Card back">
  <div class="brand-mark"></div>
  <div class="brand-name">WATTLE BAY</div>
  <div class="web">www.wattlebay.com.au</div>
</section>

<section class="card card-front" aria-label="Card front">
  <div class="brand-lockup">
    <span class="brand-mark"></span>
    <div class="brand-name">Wattle Bay<small>Tourist Parks</small></div>
  </div>

  <div class="person">
    <div class="name">NEIL PERROW</div>
    <div class="role">DIRECTOR</div>
  </div>
  <div class="divider"></div>

  <ul class="contact">
    <li>
      <svg viewBox="0 0 16 16" aria-hidden="true"><path d="M3.6 1.2l2.4 2.6-1.2 2a9 9 0 0 0 5.4 5.4l2-1.2 2.6 2.4-1.3 2.2C8 14.6 1.4 8 1.4 2.5z"/></svg>
      0491 570 156
    </li>
    <li>
      <svg viewBox="0 0 16 16" aria-hidden="true"><path d="M1 3h14v1.2L8 9 1 4.2z M1 5.8l7 4.8 7-4.8V13H1z"/></svg>
      perrow@wattlebay.com.au
    </li>
    <li>
      <svg viewBox="0 0 16 16" aria-hidden="true"><path d="M8 1a7 7 0 1 0 0 14A7 7 0 0 0 8 1zm0 2.2a4.8 4.8 0 0 1 0 9.6 4.8 4.8 0 0 1 0-9.6z"/><circle cx="8" cy="8" r="2.6"/></svg>
      www.wattlebay.com.au
    </li>
  </ul>

  <svg class="footer-band" viewBox="0 0 600 13" preserveAspectRatio="none" aria-hidden="true">
    <rect x="0" y="0" width="600" height="13" fill="var(--sea-green)"/>
    <polygon points="0,0 392,0 388,13 0,13" fill="var(--teal)"/>
    <polygon points="392,0 396,0 392,13 388,13" fill="var(--white)"/>
  </svg>
</section>

</body>
</html>
```